Duct Manufacturing Company new to the industry needs business card and stationary design

we are sheet metal duct manufacturers looking for a business card design to fit my new business logo.
nothing to crazy that will date, but want it to stand out from the crowed.
I'm sure you guys will work it out.

Contact Information for Business Card

Glen Marsh
Director

Address
17 Dorwell St
Tarrawong NSW 2638

0438 760 514

Sales@flowbend.com.au

Font styles to use
Other font styles liked:
• BankGothic md bt

Requirements
Nice to have
• Like the idea of corner rounded to match logo
• like to keep colours flowing
• font I like sharp square not rounded

```html
<!DOCTYPE html>
<html lang="en">
<head>
<meta charset="utf-8">
<title>Flowbend Industries – Business Card</title>
<link rel="stylesheet" href="https://fonts.googleapis.com/css2?family=Michroma&display=swap">
<style>
  :root {
    --backdrop: #1b1b1b;
    --card: #ffffff;
    --brand-blue: #1a6fbf;
    --deep-blue: #0b4f9e;
    --sky-blue: #1a8ad4;
    --brand-green: #8cc63f;
    --ink: #111111;
    --on-blue: #ffffff;
  }
  * { margin: 0; padding: 0; box-sizing: border-box; }
  html, body {
    width: 1200px; height: 902px; overflow: hidden;
    background: var(--backdrop);
  }
  .card {
    position: absolute; left: 80px; top: 155px;
    width: 1040px; height: 592px;
    background: var(--card);
    border-radius: 28px;
    overflow: hidden;
    font-family: "Michroma", sans-serif;
  }
  .card__waves { position: absolute; inset: 0; width: 100%; height: 100%; }

  .brand { position: absolute; left: 60px; top: 92px; width: 420px; }
  .brand__dot {
    display: block; width: 110px; height: 110px; border-radius: 50%;
    background: var(--brand-green); margin: 0 0 26px 150px;
  }
  .brand__name {
    color: var(--brand-blue); font-size: 38px; line-height: 52px;
    letter-spacing: 1px; text-transform: uppercase;
  }

  .person { position: absolute; right: 56px; top: 104px; text-align: right; }
  .person__name {
    color: var(--brand-blue); font-size: 34px; font-weight: 400; letter-spacing: 5px;
    text-transform: uppercase; line-height: 44px;
  }
  .person__role {
    color: var(--ink); font-size: 21px; letter-spacing: 3px;
    font-variant: small-caps; line-height: 30px;
  }

  .contacts { position: absolute; right: 56px; top: 250px; list-style: none; }
  .contacts__item {
    display: flex; align-items: center; justify-content: flex-end;
    height: 36px; gap: 12px;
    color: var(--ink); font-size: 20px; letter-spacing: 3px;
  }
  .contacts__item--caps { font-variant: small-caps; }
  .contacts__icon {
    width: 30px; height: 30px; border-radius: 5px;
    background: var(--brand-green);
    display: flex; align-items: center; justify-content: center;
  }
  .contacts__icon svg { width: 20px; height: 20px; }

  .address {
    position: absolute; right: 56px; top: 474px; text-align: right;
    color: var(--on-blue); font-size: 20px; letter-spacing: 3px;
    font-style: normal; font-variant: small-caps; line-height: 38px;
  }
</style>
</head>
<body>
<main class="card">
  <svg class="card__waves" viewBox="0 0 940 535" preserveAspectRatio="none" aria-hidden="true">
    <defs>
      <linearGradient id="blueBand" x1="0" y1="0" x2="0" y2="1">
        <stop offset="0" stop-color="var(--sky-blue)"/>
        <stop offset="1" stop-color="var(--deep-blue)"/>
      </linearGradient>
    </defs>
    <path d="M0 400 Q420 368 880 396 Q420 390 0 465 Z" fill="var(--brand-green)"/>
    <path d="M0 488 Q460 405 940 412 L940 535 L0 535 Z" fill="url(#blueBand)"/>
  </svg>

  <div class="brand">
    <span class="brand__dot"></span>
    <p class="brand__name">Flowbend<br>Industries</p>
  </div>

  <header class="person">
    <h1 class="person__name">Glen Marsh</h1>
    <p class="person__role">Director</p>
  </header>

  <ul class="contacts">
    <li class="contacts__item">0438 760 514
      <span class="contacts__icon"><svg viewBox="0 0 20 20"><rect x="6" y="2" width="8" height="16" rx="1.5" fill="none" stroke="#fff" stroke-width="1.6"/><rect x="8" y="4.5" width="4" height="5" fill="#fff"/></svg></span>
    </li>
    <li class="contacts__item">02 6173 4408
      <span class="contacts__icon"><svg viewBox="0 0 20 20"><path d="M3 8 Q10 3 17 8 L15 10 L12.5 8.5 L12.5 7 Q10 6 7.5 7 L7.5 8.5 L5 10 Z" fill="#fff"/><rect x="5" y="11" width="10" height="6" rx="1" fill="#fff"/></svg></span>
    </li>
    <li class="contacts__item contacts__item--caps">Sales@flowbend.com.au
      <span class="contacts__icon"><svg viewBox="0 0 20 20"><rect x="3" y="5" width="14" height="10" fill="none" stroke="#fff" stroke-width="1.6"/><path d="M3 5 L10 11 L17 5" fill="none" stroke="#fff" stroke-width="1.6"/></svg></span>
    </li>
    <li class="contacts__item contacts__item--caps">www.flowbend.com.au
      <span class="contacts__icon"><svg viewBox="0 0 20 20" fill="none" stroke="#fff" stroke-width="1.4"><circle cx="10" cy="10" r="7"/><ellipse cx="10" cy="10" rx="3" ry="7"/><path d="M3 10 H17 M4.5 6 H15.5 M4.5 14 H15.5"/></svg></span>
    </li>
  </ul>

  <address class="address">
    17 Dorwell St<br>
    Tarrawong NSW 2638
  </address>
</main>
</body>
</html>
```